PowerPoint Listing Presentation for Real Estate Agency

We need a PowerPoint presentation for a new real estate brokerage team.

[[[[[[submit 1-3 sample slides for review - i will provide feedback and you can make changes if you want to - we will not be deciding on a design prior to the deadline]]]]]

******ATTN: DESIGNERS, if your skills are webdesign then just look at this like a portable website or a brochure. it should be easy enough******

NOTE: we have all the data to put into the slides. You just need to come up with the design and layout. we have a sample design that we like and have provided.

This focus will be for the home listing side of the business (a presentation for home sellers to convince them to use our services). The data and slides will present our team and the benefits, in the best light, to use our services over that of other real estate agent applying for the job. This presentation will proved facts and benefits and describe our special and unique offerings that will show a home seller why we can sell their home for more money in less time and with the least amount of hassle. The main color scheme is Dark Blue and White (we want some additional colors included - based on your creativity. otherwise the presentation will too monotone). We would like to see the use of Statistical Graphs (3-D) - data provided. We have photos of our team and a new logo (the logo could have some minor adjustment to clean it up if necessary) - also uploaded. We have about 80-90% of the information that will be put into the slides and will need to work closely to get the design and data integrated into the presentation (should be easier then it sounds). We should be able to add slides and data 'at will' over time via our master slides built into the presentation. We have a pretty good sample presentation that we like and can be used as a guideline (this is from our affiliated business network and we have full rights to all the information), it is uploaded but doesn't contain all the slide because of size limitations.

NOTE: An additional buyers presentation will be needed after we get the sellers presentation completed, which means additional work.

This should be enough to get you started and we are available if you have any questions to help you with the project. there will be around 60-70 total slides. once concept is completed it will be easy to create the slides.

Target Market(s)

home sellers. people who are moving to a new and better home or relocation for job reasons. typically more established in life

Industry/Entity Type

Real Estate

Requirements
Must have
• all the slides must be congruent. in other words, the exact same layout feel should used across the board. we are working on building our trade dress/image. Also, it must have a soft and inviting overall feel, yet show strength of ability.
Nice to have
• nice to have use of real people images when necessary. 3D graphs would be nice. clean modern look and feel, yet sophisticated and professional.
Should not have
• should not have a lot of time consuming transitions. do not include 3D stick figures or distracting moving gifs

```html
<!DOCTYPE html>
<html lang="en">
<head>
<meta charset="utf-8">
<title>Project Title Here</title>
<link rel="stylesheet" href="https://fonts.googleapis.com/css2?family=Carlito:wght@400;700&display=swap">
<style>
  :root {
    --navy: #16175a;
    --title-blue: #1c1e6e;
    --bullet-blue: #3b40c4;
    --body-grey: #55575c;
    --copyright: #9c9cf2;
    --page-ink: #111111;
    --paper: #ffffff;
    --paper-shade: #eeeef0;
  }
  * { box-sizing: border-box; margin: 0; padding: 0; }
  html, body {
    width: 1200px; height: 900px; overflow: hidden;
    background: var(--paper);
  }
  .slide {
    position: relative; width: 1200px; height: 900px; overflow: hidden;
    font-family: "Carlito", "Calibri", sans-serif;
    background:
      radial-gradient(ellipse 900px 260px at 700px 120px, rgba(255,255,255,0.95), rgba(255,255,255,0) 70%),
      linear-gradient(160deg, #f7f7f8 0%, #ececee 45%, #f4f4f6 70%, #e9e9ec 100%);
  }
  .top-band {
    position: absolute; left: 0; top: 0; width: 1200px; height: 42px;
    background: var(--navy);
  }
  .skyline-art {
    position: absolute; left: 592px; top: 240px; width: 608px; height: 578px;
    background: linear-gradient(180deg, rgba(215,215,218,0.25) 0%, rgba(210,210,214,0.6) 55%, rgba(220,220,224,0.45) 100%);
  }
  .title {
    position: absolute; left: 57px; top: 108px;
    font-size: 46px; font-weight: 400; color: var(--title-blue);
    letter-spacing: 0.2px;
  }
  .intro {
    position: absolute; left: 51px; top: 189px; width: 1050px;
    font-size: 23px; line-height: 37.5px; color: var(--body-grey);
  }
  .points {
    position: absolute; left: 70px; top: 378px; list-style: none;
  }
  .points li {
    height: 61.5px; display: flex; align-items: flex-start;
    font-size: 31px; color: var(--body-grey);
  }
  .points li::before {
    content: "\00BB"; width: 47px; color: var(--bullet-blue);
    font-size: 28px; padding-top: 1px;
  }
  .footer-band {
    position: absolute; left: 0; top: 810px; width: 1200px; height: 90px;
  }
  .page-number {
    position: absolute; left: 36px; top: 843px;
    font-size: 24px; font-weight: 700; color: var(--page-ink);
  }
  .copyright {
    position: absolute; left: 267px; top: 846px;
    font-size: 24px; color: var(--copyright);
  }
  .brand-mark {
    position: absolute; left: 1042px; top: 787px; width: 104px; height: 104px;
    background: var(--paper); border: 3px solid var(--navy);
    display: flex; align-items: center; justify-content: center; text-align: center;
    font-size: 19px; font-weight: 700; line-height: 22px; color: var(--navy);
  }
</style>
</head>
<body>
<main class="slide">
  <div class="top-band"></div>
  <div class="skyline-art" role="img" aria-label="Faint grey city skyline of office buildings"></div>

  <h1 class="title">Project Title Here</h1>
  <p class="intro">Lorem ipsum dolor sit ipsum Lorem ipsum dolor sit ipsum Lorem ipsum dolor sit ipsum Lorem ipsum dolor sit ipsum Lorem ipsum dolor sit ipsum Lorem ipsum Lorem ipsum dolor sit ipsum Lorem ipsum dolor sit ipsum Lorem ipsum dolor sit ipsum Lorem ipsum dolor sit ipsum Lorem ipsum dolor sit ipsum Lorem ipsum</p>

  <ul class="points">
    <li>Lorem ipsum dolor sit ipsum</li>
    <li>Lorem ipsum dolor sit ipsum</li>
    <li>Lorem ipsum dolor sit ipsum</li>
    <li>Lorem ipsum dolor sit ipsum</li>
    <li>Lorem ipsum dolor sit ipsum</li>
  </ul>

  <svg class="footer-band" viewBox="0 0 1200 90" aria-hidden="true">
    <path d="M147 90 L210 22 Q226 8 250 8 L1200 8 L1200 90 Z" fill="var(--navy)"/>
  </svg>
  <div class="page-number">Page : 02</div>
  <div class="copyright">Copyright text here</div>
  <div class="brand-mark">Harlow &amp; Reed</div>
</main>
</body>
</html>
```